TPW other templates

1) Internal pages for the documents that we write. basically what will the pages inside look like. It should basically be a document with a header, a footer and a page number locator. It should include the following information: name of the report, date, TPW logo somehow, and version (draft, final etc). the information should be divided between header and footer. let me know if its unclear. As with everything it should work both in black and white and in color in case it is printed in black and white :-)
2) chapter dividers. This are the pages that you might have inside the report to separate sections. It should just have a page number, and chapter or section name. Simple, but again follow the same idea of the design that you created. It should be possible to have a picture in the divider, but it should not be a must. so in that sense we need to versions.
3) Business cards. Should include space for name, title, phone numbers (2 or 3), email, Skype, web page, and the company address which you have already.
4) a signature for emails. Basically the file that is glued to the bottom off all emails as a signature. Again it should include all the information in the business cards.

Not including any files since you have already designed others

```html
<!DOCTYPE html>
<html lang="en">
<head>
<meta charset="utf-8">
<title>TPW Email Signature</title>
<link href="https://fonts.googleapis.com/css2?family=Quicksand:wght@400;500;600&display=swap" rel="stylesheet">
<style>
  :root {
    --brand-blue: #243a8f;
    --text-grey: #5a5a5a;
    --muted-grey: #7a7a7a;
    --wash-strong: rgba(185, 214, 230, 0.55);
    --wash-soft: rgba(207, 227, 238, 0);
    --rule-blue: #a9cfe0;
    --icon-blue: #3f8fc0;
    --page: #ffffff;
  }
  html, body {
    margin: 0;
    padding: 0;
    width: 1200px;
    height: 1000px;
    overflow: hidden;
    background: var(--page);
    font-family: "Quicksand", sans-serif;
  }
  .signature {
    position: absolute;
    left: 190px;
    top: 250px;
    width: 860px;
    height: 500px;
  }
  .signature__backdrop {
    position: absolute;
    left: -65px;
    top: 229px;
    width: 793px;
    height: 226px;
    border-radius: 0 0 120px 60px;
    background: linear-gradient(100deg, var(--wash-strong) 0%, var(--wash-strong) 40%, var(--wash-soft) 100%);
  }
  .brand {
    position: absolute;
    left: 0;
    top: 0;
  }
  .brand__name {
    margin: 0;
    font-size: 108px;
    line-height: 1;
    font-weight: 600;
    color: var(--brand-blue);
    letter-spacing: 2px;
  }
  .brand__tagline {
    margin: 6px 0 0 2px;
    font-size: 17px;
    font-weight: 500;
    color: var(--brand-blue);
  }
  .brand__address {
    margin: 8px 0 0 2px;
    font-size: 19px;
    font-weight: 500;
    color: var(--muted-grey);
  }
  .person {
    position: absolute;
    left: 2px;
    top: 238px;
  }
  .person__name {
    margin: 0;
    font-size: 40px;
    font-weight: 500;
    color: var(--text-grey);
  }
  .person__title {
    margin: 2px 0 0;
    font-size: 37px;
    font-weight: 500;
    color: var(--text-grey);
  }
  .divider {
    position: absolute;
    left: -20px;
    top: 354px;
    width: 680px;
    height: 2px;
    background: var(--rule-blue);
  }
  .contact-row {
    position: absolute;
    left: 0;
    width: 800px;
    height: 36px;
    color: var(--text-grey);
    font-weight: 500;
  }
  .contact-row--phones { top: 384px; font-size: 28px; }
  .contact-row--online { top: 444px; font-size: 24px; }
  .contact {
    position: absolute;
    top: 0;
    display: flex;
    align-items: center;
    gap: 10px;
    white-space: nowrap;
  }
  .contact__icon { width: 24px; height: 24px; flex: none; }
  .separator {
    position: absolute;
    top: 4px;
    width: 2px;
    height: 28px;
    background: var(--text-grey);
  }
</style>
</head>
<body>
  <section class="signature" aria-label="TPW email signature">
    <div class="signature__backdrop" role="img" aria-label="Soft light-blue wave decoration behind the contact details"></div>

    <header class="brand">
      <p class="brand__name">TPW</p>
      <p class="brand__tagline">Tidewater Planning Works</p>
      <p class="brand__address">Kestrel Allé 7, 0261 Lindvik, Norway.</p>
    </header>

    <div class="person">
      <p class="person__name">Erik Dahl</p>
      <p class="person__title">Managing Director</p>
    </div>

    <div class="divider"></div>

    <div class="contact-row contact-row--phones">
      <span class="contact" style="left:0">
        <svg class="contact__icon" viewBox="0 0 24 24" aria-hidden="true"><path d="M6 2 L10 6 L8 9 C9 12 12 15 15 16 L18 14 L22 18 L19 22 C10 22 2 14 2 5 Z" fill="var(--icon-blue)"/></svg>
        +47 21555019
      </span>
      <span class="separator" style="left:236px"></span>
      <span class="contact" style="left:262px">+47 21555020</span>
      <span class="separator" style="left:466px"></span>
      <span class="contact" style="left:492px">+47 21555021</span>
    </div>

    <div class="contact-row contact-row--online">
      <span class="contact" style="left:0">
        <svg class="contact__icon" viewBox="0 0 24 24" aria-hidden="true"><rect x="2" y="5" width="20" height="14" fill="var(--icon-blue)"/><path d="M2 5 L12 13 L22 5" fill="none" stroke="#fff" stroke-width="1.6"/></svg>
        post@tpw.no
      </span>
      <span class="contact" style="left:250px">
        <svg class="contact__icon" viewBox="0 0 24 24" aria-hidden="true"><circle cx="12" cy="12" r="10" fill="var(--icon-blue)"/></svg>
        www.tpw.no
      </span>
      <span class="contact" style="left:500px">
        <svg class="contact__icon" viewBox="0 0 24 24" aria-hidden="true"><circle cx="12" cy="12" r="10" fill="var(--icon-blue)"/></svg>
        Erik.Dahl
      </span>
    </div>
  </section>
</body>
</html>
```